Website design for luxury private hair salon

I'm looking for someone to use my Logo and build me a website for my webpage www.corsetresses.com.au (You can have a look at it as it has every detail I need included on it already), however I want a fresh new appearance and it to look and feel super stylish.

I am thinking colours in black, with silver or white, beautiful hair images like the ones you'll see on the current webpage - the price list as per what you already see.

I will include a copy of my biz card on here, so you can see the feel of the card, and design a website with a similar feel. It is matt black with a foil silver.

Modern, but classic and fresh. I will also need you to be able to publish it to my URL for me as I have no idea how to do this. I need it up and running pronto!

The website will need to be able to be read clearly on all devices incluing smart phones and ipads. The URL is currently registered and hosted by Norvel Web

Thinking a Home Page - large logo etc and write up on who and what we offer
Services/Price List page - as per the price list on my current webpage
Contact Page - with a built in contact form.

Target Market(s)

Middle aged, fashionable, stylish women and men who enjoy luxury hair care and styling in an upmarket location.

Industry/Entity Type

Hair And Beauty

Number of Pages Required

3 page

Font styles to use
Other font styles liked:
• see my images for my current logo

Colors
000000
b2b2b2
a54499

Requirements
Must have
• Style
• Fast turnaround
• Be viewable on all devices, PC, ipads, smart phones
• Designer able to upload it so its a running website for me to my URL
Nice to have
• Just a really feminine, stylish website which is easy to read and shows some beautiful images of perfect hair
Should not have
• Browns, reds or orange colours.

```html
<!DOCTYPE html>
<html lang="en">
<head>
<meta charset="utf-8">
<title>Velour hair &amp; body</title>
<link href="https://fonts.googleapis.com/css2?family=Raleway:wght@300;400;500&family=Great+Vibes&display=swap" rel="stylesheet">
<style>
  :root {
    --ink: #000000;
    --page: #2d2d33;
    --topbar: #232328;
    --nav: #35353c;
    --silver: #b2b2b2;
    --white: #f4f4f6;
    --orchid: #a54499;
    --orchid-light: #c46bbb;
  }
  * { margin: 0; padding: 0; box-sizing: border-box; }
  html, body { width: 1200px; height: 1200px; overflow: hidden; background: var(--ink); }
  body { font-family: "Raleway", sans-serif; color: var(--white); }
  .site { width: 1200px; height: 1200px; background: var(--page); position: relative; overflow: hidden; }

  .contact-strip {
    height: 56px; background: var(--topbar);
    display: flex; align-items: center; padding-left: 130px;
    font-size: 13px; letter-spacing: .5px; color: var(--silver); gap: 10px;
  }
  .contact-strip svg { width: 16px; height: 16px; }

  .masthead {
    height: 100px; background: var(--nav);
    display: flex; align-items: center; justify-content: space-between;
    padding: 0 70px 0 130px; position: relative;
  }
  .brand { font-weight: 300; font-size: 40px; color: var(--white); line-height: 1; letter-spacing: 1px; }
  .brand small { display: block; font-size: 11px; letter-spacing: 2px; margin-top: 4px; text-align: right; }
  .masthead-right { display: flex; flex-direction: column; align-items: flex-end; gap: 14px; }
  .social { display: flex; gap: 22px; }
  .social span { width: 18px; height: 18px; border: 1.5px solid var(--silver); border-radius: 50%; display: block; }
  .menu { display: flex; align-items: center; gap: 16px; font-size: 14px; color: var(--white); }
  .menu .current { color: var(--orchid-light); }
  .menu .sep { color: var(--silver); }
  .book-btn {
    margin-left: 20px; background: var(--orchid); color: var(--white);
    font-size: 13px; font-weight: 500; padding: 10px 20px; border-radius: 18px;
  }

  .hero { position: relative; height: 620px; background: linear-gradient(90deg, #2d2d33 0%, #3a3a41 45%, #2d2d33 100%); }
  .hero-photo {
    position: absolute; left: 160px; top: 0; width: 520px; height: 620px;
    background: radial-gradient(ellipse at 55% 45%, #8d8d94 0%, #55555c 45%, #2f2f35 80%);
  }
  .hero-brand { position: absolute; left: 720px; top: 110px; text-align: center; width: 380px; }
  .hero-brand .name { font-weight: 300; font-size: 130px; line-height: 1; color: var(--white); letter-spacing: 2px; }
  .hero-brand .sub { font-size: 32px; letter-spacing: 3px; color: var(--white); margin-top: 6px; }
  .tagline { font-family: "Great Vibes", cursive; font-size: 54px; line-height: 1.25; color: var(--white); margin-top: 30px; }

  .about { position: relative; height: 424px; background: #28282d; }
  .about-photo {
    position: absolute; inset: 0;
    background: linear-gradient(100deg, #2a2a30 0%, #3b3640 45%, #4a4553 70%, #2e2c34 100%);
  }
  .about-copy { position: relative; padding: 60px 0 0 130px; }
  .about-copy h2 { font-weight: 400; font-size: 44px; }
  .about-copy h2 em { font-family: "Great Vibes", cursive; font-style: normal; color: var(--orchid-light); font-size: 50px; }
  .about-copy p { margin-top: 24px; font-size: 18px; color: var(--white); }
</style>
</head>
<body>
<div class="site">
  <div class="contact-strip">
    <svg viewBox="0 0 24 24" fill="none" stroke="#b2b2b2" stroke-width="1.6"><path d="M5 3h4l2 5-2.5 1.5a11 11 0 0 0 6 6L16 13l5 2v4a2 2 0 0 1-2 2A16 16 0 0 1 3 5a2 2 0 0 1 2-2z"/></svg>
    <span>ANA 0400 555 182 , KATE 0400 555 347</span>
  </div>

  <header class="masthead">
    <div class="brand">Velour<small>hair &amp; body</small></div>
    <div class="masthead-right">
      <div class="social"><span></span><span></span><span></span><span></span></div>
      <nav class="menu">
        <span class="current">Home</span><span class="sep">|</span>
        <span>Services &amp; Price List</span><span class="sep">|</span>
        <span>Contact us</span>
        <span class="book-btn">BOOK AN APPOINTMENT</span>
      </nav>
    </div>
  </header>

  <section class="hero">
    <div class="hero-photo" role="img" aria-label="Black and white portrait of a woman with voluminous hair and a fur-trimmed hood"></div>
    <div class="hero-brand">
      <div class="name">Velour</div>
      <div class="sub">hair &amp; body</div>
      <div class="tagline">Loves the Hair<br>You Hate.</div>
    </div>
  </section>

  <section class="about">
    <div class="about-photo" role="img" aria-label="Close-up of a woman with sleek dark hair and shimmering eye makeup"></div>
    <div class="about-copy">
      <h2>About <em>us</em></h2>
      <p>'We pride ourselves on being able to offer a private salon experience</p>
    </div>
  </section>
</div>
</body>
</html>
```